Local fast-growing company in the service sector

We are looking for a modern business card design, which should also appear on our letterheads

Target Market(s)

Private and industrial sectors

Contact Information for Business Card

Vorname Name
Kellberger Str. 18
74821 Brenzfeld
Tel.: 07146-839214-0
Name@agentur-kvtl.de

Colors
9d9d9d
919191
aaaaaa

Requirements
Must have
• The logo (file) in silver

```html
<!DOCTYPE html>
<html lang="de">
<head>
<meta charset="utf-8">
<title>KVTL Visitenkarte</title>
<link rel="stylesheet" href="https://fonts.googleapis.com/css2?family=Montserrat:wght@400;500;700;800&display=swap">
<style>
  :root {
    --page-bg: #e6e6e6;
    --card-dark: #2b2b2b;
    --card-dark-center: #3d3d3d;
    --card-light: #f4f4f4;
    --silver: #aaaaaa;
    --silver-light: #c4c4c4;
    --ink: #1f1f1f;
    --ink-soft: #2e2e2e;
  }
  * { margin: 0; padding: 0; box-sizing: border-box; }
  html, body {
    width: 1200px; height: 576px; overflow: hidden;
    background: var(--page-bg);
    font-family: "Montserrat", sans-serif;
  }
  .canvas { position: relative; width: 1200px; height: 576px; }

  .card {
    position: absolute;
    border-radius: 11px;
    overflow: hidden;
    box-shadow: 0 2px 5px rgba(0,0,0,0.25);
  }
  .card-front {
    left: 82px; top: 139px; width: 484px; height: 293px;
    background: radial-gradient(ellipse at 50% 35%, var(--card-dark-center) 0%, var(--card-dark) 70%);
  }
  .card-back {
    left: 602px; top: 138px; width: 481px; height: 292px;
    background: var(--card-light);
  }
  .card-back .shape { position: absolute; inset: 0; width: 100%; height: 100%; }

  .brand {
    position: absolute;
    display: flex; flex-direction: column; align-items: center;
    color: var(--silver-light);
  }
  .brand-name {
    font-weight: 800;
    letter-spacing: 2px;
    line-height: 1;
  }
  .brand-url {
    font-weight: 500;
    letter-spacing: 1px;
    color: var(--silver);
  }
  .brand-mark {
    width: 14px; height: 14px;
    background: var(--silver);
    margin-bottom: 10px;
  }
  .card-front .brand { left: 0; right: 0; top: 108px; }
  .card-front .brand-name { font-size: 52px; }
  .card-front .brand-url { font-size: 15px; margin-top: 4px; }

  .card-back .brand { left: 18px; width: 170px; top: 92px; }
  .card-back .brand-name { font-size: 44px; }
  .card-back .brand-url { font-size: 12.5px; margin-top: 4px; }

  .person-name {
    position: absolute; right: 28px; top: 34px;
    font-weight: 800; font-size: 15px; letter-spacing: 1.6px;
    color: var(--ink);
  }
  .contact {
    position: absolute; right: 28px; top: 170px;
    text-align: right;
    font-size: 12px; font-weight: 500;
    color: var(--ink-soft);
    line-height: 17px;
  }
  .address { margin-right: 16px; margin-bottom: 6px; }
  .contact-line { display: flex; justify-content: flex-end; align-items: center; gap: 6px; }
  .contact-line svg { width: 10px; height: 10px; fill: var(--ink-soft); }
</style>
</head>
<body>
<div class="canvas">

  <section class="card card-front">
    <div class="brand">
      <span class="brand-mark"></span>
      <span class="brand-name">KVTL</span>
      <span class="brand-url">agentur-kvtl.de</span>
    </div>
  </section>

  <section class="card card-back">
    <svg class="shape" viewBox="0 0 481 292" preserveAspectRatio="none" aria-hidden="true">
      <path d="M0 0 H166 Q268 146 190 292 H0 Z" fill="#2d2d2d"/>
      <path d="M180 0 H188 Q286 146 204 292 H197 Q276 146 180 0 Z" fill="#2b2b2b"/>
    </svg>

    <div class="brand">
      <span class="brand-mark"></span>
      <span class="brand-name">KVTL</span>
      <span class="brand-url">agentur-kvtl.de</span>
    </div>

    <h1 class="person-name">VORNAME NAME</h1>

    <div class="contact">
      <p class="address">Kellberger Str. 18<br>74821 Brenzfeld</p>
      <p class="contact-line">07146-839214-0
        <svg viewBox="0 0 10 10"><path d="M1 3 Q5 0 9 3 L8 4.5 L6.5 3.8 V3 Q5 2.5 3.5 3 V3.8 L2 4.5 Z M2.5 5 H7.5 L8.5 9 H1.5 Z"/></svg>
      </p>
      <p class="contact-line">Name@agentur-kvtl.de
        <svg viewBox="0 0 10 10"><path d="M0.5 2 H9.5 V8 H0.5 Z M1.3 2.6 L5 5.5 L8.7 2.6" stroke="#fff" stroke-width="0.7"/></svg>
      </p>
      <p class="contact-line">www.agentur-kvtl.de
        <svg viewBox="0 0 10 10"><circle cx="5" cy="5" r="4.5"/><path d="M5 0.5 V9.5 M0.5 5 H9.5 M5 0.5 Q2 5 5 9.5 M5 0.5 Q8 5 5 9.5" stroke="#fff" stroke-width="0.6" fill="none"/></svg>
      </p>
    </div>
  </section>

</div>
</body>
</html>
```